Upmarket Dessert Lounge needs a Business Card Design

We are an upmarket dessert lounge needing a business card to match our image.

We want something that is simple yet beautiful, feminine, classy, sophisticated and elegant. We want it to stand out and don't mind if it is bold.

The design should include our logo and colours of red or maroon with gold highlights. We don't mind if black is used.

Marlow & Quince

Target Market(s)

For those who like to indulge or treat themselves and give in to their temptations on good quality desserts.

Industry/Entity Type

Business

Requirements
Must have
• Must include our logo and our name

Marlow & Quince

M & Q

```html
<!DOCTYPE html>
<html lang="en">
<head>
<meta charset="utf-8">
<title>Marlow &amp; Quince — Business Card</title>
<link rel="stylesheet" href="https://fonts.googleapis.com/css2?family=Tinos:wght@400;700&display=swap">
<style>
  :root {
    --stage: #e9e4de;
    --navy: #0b1128;
    --maroon: #7a1516;
    --cream: #f6cf9e;
    --white: #ffffff;
    --rule: rgba(255,255,255,0.55);
  }
  * { box-sizing: border-box; margin: 0; padding: 0; }
  html, body { width: 1200px; height: 417px; overflow: hidden; }
  body {
    background: var(--stage);
    position: relative;
    font-family: "Tinos", "Times New Roman", serif;
  }
  .card {
    position: absolute;
    top: 61px;
    width: 515px;
    height: 294px;
    border-radius: 12px;
    background: var(--navy);
    overflow: hidden;
    box-shadow: 0 3px 8px rgba(0,0,0,0.25);
  }
  .card--front { left: 54px; }
  .card--back { left: 630px; }

  .brand-name {
    position: absolute;
    left: 0; right: 0;
    text-align: center;
    color: var(--cream);
    font-size: 30px;
    font-weight: 400;
    letter-spacing: 1px;
    text-transform: uppercase;
  }
  .card--front .brand-name { top: 72px; }
  .card--back .brand-name { top: 106px; }

  .front-wave { position: absolute; left: 0; top: 0; width: 515px; height: 294px; }

  .holder {
    position: absolute;
    top: 215px; left: 0; right: 0;
    text-align: center;
    color: var(--white);
    font-size: 16px;
  }
  .holder__name { font-weight: 700; }
  .holder__title { font-size: 14px; }

  .contact {
    position: absolute;
    top: 248px; left: 0; right: 0;
    color: var(--white);
    font-size: 12.5px;
    line-height: 19px;
  }
  .contact__col { position: absolute; top: 0; }
  .contact__address { left: 48px; width: 116px; text-align: center; }
  .contact__phones { left: 190px; padding-left: 5px; }
  .contact__web { left: 340px; }
  .contact__divider {
    position: absolute;
    top: 2px;
    width: 1px;
    height: 36px;
    background: var(--rule);
  }
  .contact__divider--one { left: 180px; }
  .contact__divider--two { left: 329px; }
  .contact__line { display: flex; align-items: center; gap: 7px; white-space: nowrap; }
  .icon { width: 10px; height: 10px; fill: var(--white); flex: none; }

  .back-url {
    position: absolute;
    top: 223px; left: 0; right: 0;
    text-align: center;
    color: var(--white);
    font-size: 15px;
    letter-spacing: 2.5px;
  }
</style>
</head>
<body>
  <section class="card card--front" aria-label="Business card front">
    <svg class="front-wave" viewBox="0 0 515 294" aria-hidden="true">
      <path d="M0 170 C120 190 230 200 320 196 C400 192 460 196 515 210 L515 216 C440 202 370 205 300 210 C200 218 100 212 0 196 Z" fill="var(--cream)"/>
      <path d="M0 200 C100 214 200 220 300 212 C380 206 450 208 515 218 L515 294 L0 294 Z" fill="var(--maroon)"/>
    </svg>

    <h1 class="brand-name">Marlow &amp; Quince</h1>

    <p class="holder"><span class="holder__name">YOUR NAME,</span> <span class="holder__title">Title</span></p>

    <div class="contact">
      <div class="contact__col contact__address">
        <div>00, Complex name</div>
        <div>City, State 000 000</div>
      </div>
      <span class="contact__divider contact__divider--one"></span>
      <div class="contact__col contact__phones">
        <div class="contact__line">
          <svg class="icon" viewBox="0 0 10 10"><path d="M2 0.5 L3.6 2.6 L2.8 3.6 C3.4 5 4.8 6.4 6.2 7 L7.2 6.2 L9.5 7.8 L8.4 9.5 C4.5 9.3 0.7 5.5 0.5 1.6 Z"/></svg>
          <span>+2348100457391</span>
        </div>
        <div class="contact__line">
          <svg class="icon" viewBox="0 0 10 10"><path d="M2.5 0 H7.5 V10 H2.5 Z M3.3 1.2 V7.6 H6.7 V1.2 Z"/><rect x="4.4" y="8.2" width="1.2" height="1" fill="var(--maroon)"/></svg>
          <span>+2348100457391</span>
        </div>
      </div>
      <span class="contact__divider contact__divider--two"></span>
      <div class="contact__col contact__web">
        <div class="contact__line">
          <svg class="icon" viewBox="0 0 10 10"><path d="M0.5 2 H9.5 V8 H0.5 Z"/><path d="M0.5 2 L5 5.5 L9.5 2" fill="none" stroke="var(--maroon)" stroke-width="0.8"/></svg>
          <span>hello@marlowquince.com</span>
        </div>
        <div class="contact__line">
          <svg class="icon" viewBox="0 0 10 10"><circle cx="5" cy="5" r="4.5"/><path d="M0.5 5 H9.5 M5 0.5 C3 3 3 7 5 9.5 M5 0.5 C7 3 7 7 5 9.5" fill="none" stroke="var(--maroon)" stroke-width="0.7"/></svg>
          <span>www.marlowquince.com</span>
        </div>
      </div>
    </div>
  </section>

  <section class="card card--back" aria-label="Business card back">
    <h2 class="brand-name">Marlow &amp; Quince</h2>
    <p class="back-url">www.marlowquince.com</p>
  </section>
</body>
</html>
```